Accounting firm needing business card / letterhead designed
Marcus L. Trenholm, CPA
marcus@veltrowledger.com
www.veltrowledger.com
842 E Alder Ave Carrow Falls, WA 43827
555-562-0974

```html
<!DOCTYPE html>
<html lang="en">
<head>
<meta charset="utf-8">
<title>Veltrow Ledger — Business Card</title>
<link rel="stylesheet" href="https://fonts.googleapis.com/css2?family=PT+Sans:ital,wght@0,400;0,700;1,400&display=swap">
<style>
  :root {
    --backdrop: #3a332f;
    --card: #161616;
    --card-edge: #222222;
    --brand-purple: #3d3592;
    --ink-light: #f2f2f2;
    --ink-muted: #bdbdbd;
    --rule: #d9d9d9;
  }
  * { margin: 0; padding: 0; box-sizing: border-box; }
  html, body {
    width: 1200px; height: 864px; overflow: hidden;
    background: var(--backdrop);
    font-family: "PT Sans", Arial, sans-serif;
  }
  .stage {
    position: relative; width: 1200px; height: 864px;
    display: flex; align-items: center; justify-content: center; gap: 48px;
  }
  .card {
    position: relative; width: 540px; height: 310px;
    background: var(--card);
    border: 1px solid var(--card-edge);
    box-shadow: 0 14px 30px rgba(0,0,0,.45);
    overflow: hidden;
  }

  /* Front */
  .card-front .brand {
    position: absolute; left: 0; right: 0; top: 112px;
    text-align: center;
    font-weight: 700; font-size: 46px; letter-spacing: 3px; line-height: 56px;
    color: var(--brand-purple); text-transform: uppercase;
  }
  .card-front .website {
    position: absolute; left: 0; right: 0; top: 200px;
    text-align: center; color: var(--ink-muted);
    font-size: 14px; letter-spacing: 6px;
  }

  /* Back */
  .card-back .brand {
    position: absolute; right: 28px; top: 76px;
    font-weight: 700; font-size: 34px; letter-spacing: 2px; line-height: 40px;
    color: var(--brand-purple); text-transform: uppercase;
  }
  .card-back .person {
    position: absolute; left: 28px; top: 124px;
    color: var(--brand-purple); font-size: 16px; font-style: italic;
  }
  .card-back .divider {
    position: absolute; left: 28px; right: 28px; top: 150px;
    height: 1px; background: var(--rule);
  }
  .contact-list {
    position: absolute; left: 28px; top: 164px;
    list-style: none; color: var(--ink-light); font-size: 14px; line-height: 20px;
  }
  .contact-list li { display: flex; align-items: center; gap: 7px; }
  .contact-list svg { width: 10px; height: 10px; fill: var(--ink-muted); flex: none; }
  .address {
    position: absolute; right: 28px; bottom: 26px;
    text-align: right; color: var(--ink-light); font-size: 16px; line-height: 20px;
    font-style: normal;
  }
</style>
</head>
<body>
<main class="stage">
  <section class="card card-front" aria-label="Card front">
    <div class="brand">Veltrow Ledger</div>
    <div class="website">www.veltrowledger.com</div>
  </section>

  <section class="card card-back" aria-label="Card back">
    <div class="brand">Veltrow Ledger</div>
    <div class="person">Marcus L. Trenholm, CPA</div>
    <div class="divider"></div>
    <ul class="contact-list">
      <li>
        <svg viewBox="0 0 10 10" aria-hidden="true"><path d="M2 0h3l1 2.5-1.5 1a6 6 0 0 0 2 2l1-1.5L10 5v3a2 2 0 0 1-2 2A8 8 0 0 1 0 2a2 2 0 0 1 2-2z"/></svg>
        555-562-0974
      </li>
      <li>
        <svg viewBox="0 0 10 10" aria-hidden="true"><path d="M0 2h10v6H0z M0 2l5 3.5L10 2" stroke="#161616" stroke-width="0.8"/></svg>
        marcus@veltrowledger.com
      </li>
      <li>
        <svg viewBox="0 0 10 10" aria-hidden="true"><circle cx="5" cy="5" r="5"/><path d="M0 5h10M5 0v10" stroke="#161616" stroke-width="0.8"/></svg>
        www.veltrowledger.com
      </li>
    </ul>
    <address class="address">842 E Alder Ave<br>Carrow Falls, WA 43827</address>
  </section>
</main>
</body>
</html>
```